Gaming company needs web presence

PLEASE NOTE: We need just a simple web site. We are at least a year away from launching our first product, so the site only needs a small amount of information on it. The only people who will be visiting the web site are prospective employees, prospective investors who want a little information on the company, journalists who want a little more information, and people in the games industry who will visit to read blog posts about the development of our first game.

Lanternfield Games is a new gaming company that wants to change how people think about video games. We are making games that we think can be so interesting to watch that people might want to tune into them instead of the TV.

The games we make are sophisticated, they are not for children, and we want to project an image of being serious about our craft and the brand we're trying to create. Our games are heavily focused on players interacting with each other in sophisticated ways: to negotiate, to compete, to fight, to come to each other's rescue, to cheer each other on, or to simply watch each other in awe.

We do not want a site that features lots of video game cliches like joysticks, 8 bit graphics, science fiction themes, or military themes. We are focused on craftsmanship, so we'd like to project a sense of precision, pride and deep purpose.

The purpose of this website is to create an image of our company that can help us recruit like-minded craftspeople and help find business partners. There will be no e-commerce, account creation, or forums for some time. The site should have:
-A front page that describes our business
-A section that describes our first game (we have only one for now)
-A section for employees to write blog posts. There should be something on the home page that shows links to the latest 3 blog posts.
-A section about founders that shows information about them.
-Contact information, lets people send us email

Our first game is one that looks very realistic. It takes place on a tropical island. We can't say a lot more about it in public yet, but I will say these things: it is not a game that children will play, it is not very violent, it would look more like a film than a typical video game.

And the site should be easily extendable when we have more content and more categories of content.

I've attached our official company logo with a color scheme we've been using, plus an alternate version of the logo. Please use this as a starting point for the web site's visual design. Also, I do not think it is necessary to use the dark background in the logo as the background throughout the site. I wouldn't rule it out, but I'd like to see some proposals with lighter backgrounds.

We need to be able to get code from you so that we can drop it on our server and get it running without extra effort. We need to be able to add content for Blog posts easily as well, so please indicate how that would work.
Updates

Hello everyone, Thanks for all of the great submissions so far. There are some important things I'd like to relay to everyone: We are at least a year away from launching our first game, so we only need a simple web site. Unfortunately, we can't share any screenshots or details about our first game yet. All of these submissions look great, but are far too complicated. Also, I really want to stress that we don't want to feature stock photography of people playing games, especially of children playing games. In fact, since we don't want to release any screenshots of our games and we don't have any good photography of ourselves working, it's best if there are no photographic images on the site for now.

Hello designers, Can you let me know if your designs include all the code that would let us drop the files on to our web server and easily get it up and running? Also, can you tell me how the blog posts would be created? Does your code run on a CMS? Thanks, Haskell

Hi Designers, we will be hosting this site with Wordpress, so we would prefer to have submissions ready to go on a Wordpress server. Thanks!

Target Market(s)

Investors, prospective employees, press, blog post readers.

Industry/Entity Type

Business

Font styles to use
Sans Serif

Requirements
Must have
• Simplicity first. Please use a color palette and fonts that match our logo.
Should not have
• Video game cliches. Flash animations or menus.
No children.
No photographs of people playing games.

(I realize this is very limiting, but we're keeping the sits as simple as possible for now)

```html
<!DOCTYPE html>
<html lang="en">
<head>
<meta charset="utf-8">
<title>Lanternfield Games</title>
<link rel="stylesheet" href="https://fonts.googleapis.com/css2?family=Josefin+Sans:wght@300;400;700&family=Arvo:wght@700&family=Lato:wght@400;700&display=swap">
<style>
:root{
  --wood-dark:#3a2414;
  --wood-mid:#5a3820;
  --wood-light:#6b4527;
  --cream:#f6f1dc;
  --cream-soft:#f9f6e8;
  --orange:#e07a2c;
  --brown-text:#4a2e1a;
  --body-text:#7a7468;
  --white:#ffffff;
  --line:#d9d2bd;
  --photo:#c9c4bb;
}
*{box-sizing:border-box;margin:0;padding:0}
html,body{width:813px;height:1200px;overflow:hidden;background:var(--white)}
body{font-family:"Lato",sans-serif;color:var(--body-text);position:relative}

.site-header{position:absolute;left:0;top:0;width:813px;height:365px;
  background:linear-gradient(180deg,var(--wood-mid) 0%,var(--wood-light) 45%,var(--wood-mid) 100%)}
.header-pointer{position:absolute;left:391px;top:364px;width:0;height:0;
  border-left:16px solid transparent;border-right:16px solid transparent;border-top:20px solid var(--wood-mid)}
.main-nav{position:absolute;left:108px;top:40px;display:flex;gap:22px}
.main-nav a{font-family:"Josefin Sans",sans-serif;font-size:10px;color:var(--cream);text-decoration:none;letter-spacing:.5px;padding-bottom:5px}
.main-nav a.is-active{border-bottom:2px solid var(--orange)}
.social-links{position:absolute;right:108px;top:38px;display:flex;gap:5px}
.social-links span{width:13px;height:13px;border-radius:50%;background:var(--cream)}
.brand-wordmark{position:absolute;left:0;top:125px;width:813px;text-align:center;
  font-family:"Josefin Sans",sans-serif;font-weight:700;color:var(--cream);line-height:1}
.brand-wordmark .top{display:block;font-size:78px;letter-spacing:3px}
.brand-wordmark .bottom{display:block;font-size:44px;letter-spacing:8px;margin-top:30px}

.tagline-band{position:absolute;left:0;top:365px;width:813px;height:135px;background:var(--cream);text-align:center;
  font-family:"Arvo",serif;font-weight:700}
.tagline-band .line-one{margin-top:46px;font-size:26px;color:var(--brown-text);letter-spacing:1px}
.tagline-band .line-two{font-size:26px;color:var(--orange);letter-spacing:1px;margin-top:4px}

.founders{position:absolute;left:108px;top:520px;width:600px}
.section-title{font-family:"Josefin Sans",sans-serif;font-size:18px;color:var(--brown-text);letter-spacing:.5px}
.founder{position:absolute;width:290px;height:130px}
.founder-photo{position:absolute;left:0;top:0;width:122px;height:122px;border-radius:50%;background:var(--photo);border:5px solid #e9e6df}
.founder-info{position:absolute;left:140px;top:6px;width:150px}
.founder-name{font-family:"Josefin Sans",sans-serif;font-size:12px;color:var(--brown-text);text-transform:uppercase}
.founder-role{font-size:8px;color:var(--orange);margin:3px 0 6px}
.founder-bio{font-size:8px;line-height:1.45}
.read-more{display:inline-block;margin-top:8px;background:var(--wood-dark);color:var(--cream);font-size:7px;padding:3px 6px;letter-spacing:.5px}

.contact{position:absolute;left:0;top:935px;width:813px;height:193px;background:var(--cream-soft)}
.contact .section-title{text-align:center;margin-top:16px;font-size:20px}
.contact-intro{text-align:center;font-size:9px;width:560px;margin:8px auto 0;line-height:1.4}
.contact-form{position:absolute;left:135px;top:88px;width:540px}
.field{position:absolute;left:0;width:268px;height:22px;background:var(--white);border:1px solid var(--line);
  font-size:8px;color:#9a9485;padding:6px 8px}
.field-message{left:278px;top:0;width:262px;height:58px}
.send-button{position:absolute;left:278px;top:66px;width:262px;height:20px;background:var(--wood-dark);color:var(--cream);
  font-size:8px;text-align:center;line-height:20px;letter-spacing:.5px}

.site-footer{position:absolute;left:0;top:1128px;width:813px;height:72px;background:var(--wood-mid)}
.footer-wordmark{position:absolute;left:108px;top:18px;font-family:"Josefin Sans",sans-serif;font-weight:700;color:var(--cream);
  font-size:15px;line-height:1.15;text-align:center;letter-spacing:1px}
.footer-meta{position:absolute;right:108px;top:30px;display:flex;align-items:center;gap:10px;font-size:8px;color:var(--cream)}
.footer-meta .dots{display:flex;gap:4px}
.footer-meta .dots span{width:11px;height:11px;border-radius:50%;background:var(--cream)}
</style>
</head>
<body>
<header class="site-header">
  <nav class="main-nav">
    <a href="#">HOME</a><a href="#" class="is-active">ABOUT US</a><a href="#">SERVICES</a><a href="#">BLOG</a><a href="#">REVIEWS</a><a href="#">CONTACT US</a>
  </nav>
  <div class="social-links" aria-label="Social links"><span></span><span></span><span></span><span></span></div>
  <div class="brand-wordmark"><span class="top">LANTERNFIELD</span><span class="bottom">GAMES</span></div>
</header>
<div class="header-pointer"></div>

<section class="tagline-band">
  <p class="line-one">THE WORLD WANTS TO SEE</p>
  <p class="line-two">YOUR SKILL AND CREATIVITY</p>
</section>

<section class="founders">
  <h2 class="section-title">FOUNDERS</h2>
  <article class="founder" style="left:0;top:50px">
    <div class="founder-photo" role="img" aria-label="Portrait of Marla Quincey"></div>
    <div class="founder-info"><h3 class="founder-name">Marla Quincey</h3><p class="founder-role">Founder and Game Director</p>
      <p class="founder-bio">We craft worlds where players meet, bargain and compete. Every system is built with patience and care so each match feels like a story worth watching.</p><span class="read-more">READ MORE</span></div>
  </article>
  <article class="founder" style="left:306px;top:50px">
    <div class="founder-photo" role="img" aria-label="Portrait of Dean Whitford"></div>
    <div class="founder-info"><h3 class="founder-name">Dean Whitford</h3><p class="founder-role">Founder and Technical Lead</p>
      <p class="founder-bio">We craft worlds where players meet, bargain and compete. Every system is built with patience and care so each match feels like a story worth watching.</p><span class="read-more">READ MORE</span></div>
  </article>
  <article class="founder" style="left:0;top:240px">
    <div class="founder-photo" role="img" aria-label="Portrait of Nolan Brecker"></div>
    <div class="founder-info"><h3 class="founder-name">Nolan Brecker</h3><p class="founder-role">Founder and Art Director</p>
      <p class="founder-bio">We craft worlds where players meet, bargain and compete. Every system is built with patience and care so each match feels like a story worth watching.</p><span class="read-more">READ MORE</span></div>
  </article>
  <article class="founder" style="left:306px;top:240px">
    <div class="founder-photo" role="img" aria-label="Portrait of Julian Amari"></div>
    <div class="founder-info"><h3 class="founder-name">Julian Amari</h3><p class="founder-role">Founder and Design Lead</p>
      <p class="founder-bio">We craft worlds where players meet, bargain and compete. Every system is built with patience and care so each match feels like a story worth watching.</p><span class="read-more">READ MORE</span></div>
  </article>
</section>

<section class="contact">
  <h2 class="section-title">CONTACT US</h2>
  <p class="contact-intro">If you'd like to join our studio, talk about partnership or ask about our first game, send us a note below and we will reply soon.</p>
  <form class="contact-form">
    <div class="field" style="top:0">Name</div>
    <div class="field" style="top:32px">Email Address</div>
    <div class="field" style="top:64px">Phone Number</div>
    <div class="field field-message">Contact Number</div>
    <div class="send-button">SEND</div>
  </form>
</section>

<footer class="site-footer">
  <div class="footer-wordmark">LANTERNFIELD<br>GAMES</div>
  <div class="footer-meta"><span>© 2016 All Rights Reserved | Privacy Policy</span><div class="dots"><span></span><span></span><span></span><span></span></div></div>
</footer>
</body>
</html>
```